Business card for marketing analytics company

Need a business card for new company. I have a logo already that I want to be built into the card and should use those colours

Company is called steered by tallies
Design must bring steered by tallies to life not be a card that could be for anyone with a logo put on it.

Like the front to be fairly clean and uncluttered bringing the logo out with a suitable design on the back of the card.

The logo represents a compass and business growth so those themes along with numbers, analytics , data are appropriate.
I'm often working with creative industries so also needs to reflect the creative side of analytics rather than be very corporate looking.

Target Market(s)

Ad agency, media agency, consumer goods clients

Industry/Entity Type

Market Research

Contact Information for Business Card

Needs to include name, title, email and phone number

Colors
f78f20
f68d4d
ec1f27

Requirements
Must have
• Must bring steered by tallies to life not be a card that could be for anyone with a logo put on it.
• Logo, Correct colours
• Like a design on the back that relates to company name
• Designs for both sides
Should not have
• Please do not just submit logo and a coloured card.
• It needs to have a design element to it
• No black background
• No clear cards - needs front & back

```html
<!DOCTYPE html>
<html lang="en">
<head>
<meta charset="utf-8">
<title>Steered by Tallies – Business Card</title>
<link rel="stylesheet" href="https://fonts.googleapis.com/css2?family=Montserrat:wght@500&family=Open+Sans:wght@400;600&display=swap">
<style>
  :root {
    --backdrop: #2b2b2b;
    --card-white: #ffffff;
    --brand-red: #be1a1f;
    --brand-orange: #f47a20;
    --deep-red: #c8202a;
    --ink: #4a4f55;
    --on-red: #ffffff;
    --faint-tint: #fbe9e4;
    --card-shadow: 0 4px 14px rgba(0, 0, 0, 0.55);
  }
  * { margin: 0; padding: 0; box-sizing: border-box; }
  html, body {
    width: 1200px;
    height: 987px;
    overflow: hidden;
    background: var(--backdrop);
  }
  .canvas {
    position: relative;
    width: 1200px;
    height: 987px;
  }
  .card {
    position: absolute;
    left: 293px;
    width: 615px;
    height: 352px;
    overflow: hidden;
    box-shadow: var(--card-shadow);
  }
  .card--front { top: 130px; background: var(--card-white); }
  .card--back  { top: 505px; background: var(--brand-red); }

  .card__decor {
    position: absolute;
    inset: 0;
    width: 100%;
    height: 100%;
  }

  .brand {
    position: absolute;
    display: flex;
    align-items: center;
    gap: 20px;
  }
  .brand__dot {
    flex: none;
    border-radius: 50%;
    border: 3px solid var(--brand-orange);
  }
  .brand__name {
    font-family: "Montserrat", sans-serif;
    font-weight: 500;
    color: var(--brand-orange);
    line-height: 1.12;
  }
  .card--front .brand { left: 50px; top: 49px; }
  .card--front .brand__dot { width: 92px; height: 92px; }
  .card--front .brand__name { font-size: 27px; }

  .card--back .brand { left: 126px; top: 116px; }
  .card--back .brand__dot { width: 114px; height: 114px; border-color: var(--on-red); }
  .card--back .brand__name { font-size: 32px; color: var(--on-red); }

  .holder {
    position: absolute;
    left: 50px;
    top: 245px;
  }
  .holder__name {
    font-family: "Open Sans", sans-serif;
    font-weight: 600;
    font-size: 21px;
    color: var(--brand-orange);
    letter-spacing: 0.2px;
  }
  .holder__title {
    font-family: "Open Sans", sans-serif;
    font-size: 16px;
    color: var(--deep-red);
    margin-top: 1px;
  }

  .contacts {
    position: absolute;
    left: 324px;
    top: 235px;
    list-style: none;
    font-family: "Open Sans", sans-serif;
    font-size: 15.5px;
    color: var(--ink);
  }
  .contacts__item {
    display: flex;
    align-items: center;
    gap: 9px;
    height: 24px;
  }
  .contacts__icon { width: 14px; height: 14px; flex: none; }
</style>
</head>
<body>
<main class="canvas">

  <section class="card card--front" aria-label="Card front">
    <svg class="card__decor" viewBox="0 0 615 352" aria-hidden="true">
      <circle cx="440" cy="174" r="130" fill="none" stroke="var(--faint-tint)" stroke-width="5"/>
    </svg>

    <div class="brand">
      <span class="brand__dot"></span>
      <div class="brand__name">Steered by<br>Tallies</div>
    </div>

    <div class="holder">
      <div class="holder__name">DANA REYES</div>
      <div class="holder__title">CEO/Founder</div>
    </div>

    <ul class="contacts">
      <li class="contacts__item">
        <svg class="contacts__icon" viewBox="0 0 16 16" aria-hidden="true">
          <path fill="#f47a20" d="M3.6 1.2l2.3 2.6-1.3 1.9c.9 2 2.6 3.7 4.6 4.6l1.9-1.3 2.6 2.3-1.4 2.4C7 13.4 2.6 9 1.2 3z"/>
        </svg>
        555 204 7813
      </li>
      <li class="contacts__item">
        <svg class="contacts__icon" viewBox="0 0 16 16" aria-hidden="true">
          <rect x="1" y="3.5" width="14" height="9.5" fill="#f47a20"/>
          <path d="M1.5 4l6.5 5 6.5-5" fill="none" stroke="#ffffff" stroke-width="1.3"/>
        </svg>
        dana@steeredbytallies.com
      </li>
      <li class="contacts__item">
        <svg class="contacts__icon" viewBox="0 0 16 16" aria-hidden="true">
          <circle cx="8" cy="8" r="7" fill="#f47a20"/>
          <path d="M1 8h14M8 1c-3 3.5-3 10.5 0 14M8 1c3 3.5 3 10.5 0 14" fill="none" stroke="#ffffff" stroke-width="1"/>
        </svg>
        www.steeredbytallies.com
      </li>
    </ul>
  </section>

  <section class="card card--back" aria-label="Card back">
    <svg class="card__decor" viewBox="0 0 615 352" aria-hidden="true">
      <g fill="none" stroke="#ffffff" stroke-opacity="0.1" stroke-width="1.5">
        <circle cx="560" cy="300" r="90"/>
        <circle cx="560" cy="300" r="150"/>
        <circle cx="560" cy="300" r="210"/>
      </g>
      <polyline points="0,330 90,300 160,315 250,270 330,285 420,220 500,235 615,150"
                fill="none" stroke="var(--brand-orange)" stroke-opacity="0.45" stroke-width="2"/>
    </svg>

    <div class="brand">
      <span class="brand__dot"></span>
      <div class="brand__name">Steered by<br>Tallies</div>
    </div>
  </section>

</main>
</body>
</html>
```